New Business Card Design for Manufacturing

We are an engineering/manufacturing company that offers Advanced machining/assembly/engineering services, as well as innovative products for the heavy duty engine cooling markets.

We are looking to get a new business card designed that is clean and modern looking, but still fits the wide range of technical/skilled work we do.

- We hope to use this design as the base for other design work in new Presentations, web, and print work.

Industry/Entity Type

Engineering

Contact Information for Business Card

Our preferred color of blue is (RGB) 22/71/159 but can vary slightly from that color. Our content will be our Logo and full company name (Vantrell Forge Works, Inc.), company address, name, job title, phone number with extension, cell number, fax number, website, and email address on the cards.
We'd like the full company name next to the logo, but we are open to other interpretations of that layout.
Preferably, we would like the back side to be clean with just our logo, and the front to contain all of the contact information.

Colors
2f74b4
0355a3
85abd2

Requirements
Must have
• - Logo, company name, needed content - We are open to interpretation beyond that.
• - Standard size business card.
• - Horizontal orientation.
• - Enough space for lengthy names / job titles (for example, a job title could read "Directory of Human Resources" or "V.P. of Governmental Affairs"). We need this to look clean, whether the title be short (CEO) or long (as described above).

```html
<!DOCTYPE html>
<html lang="en">
<head>
<meta charset="utf-8">
<title>Vantrell Forge Works – Business Card</title>
<link rel="stylesheet" href="https://fonts.googleapis.com/css2?family=Merriweather+Sans:wght@400;700&family=Open+Sans:wght@400;700&display=swap">
<style>
  :root{
    --page:#d9dcdf;
    --card-frost:#eceef0;
    --brand-blue:#16479f;
    --brand-blue-deep:#0f3c86;
    --text-light:#ffffff;
    --text-soft:#e3ebf6;
    --address:#a9c3e3;
    --logo-blue:#16479f;
  }
  *{margin:0;padding:0;box-sizing:border-box}
  html,body{width:1200px;height:1047px;overflow:hidden;background:var(--page)}
  .card{
    position:absolute;left:80px;top:213px;width:1040px;height:620px;
    background:var(--card-frost);overflow:hidden;
    box-shadow:0 10px 30px rgba(0,0,0,.18);
  }
  .card__band{position:absolute;inset:0;width:1040px;height:620px}
  .holder{position:absolute;left:57px;top:62px;color:var(--text-light)}
  .holder__name{font:700 37px/1 "Merriweather Sans",sans-serif}
  .holder__title{font:400 22px/1 "Open Sans",sans-serif;color:var(--text-soft);margin-top:16px}
  .company{position:absolute;left:57px;top:280px;color:var(--text-light);font:700 25px/1 "Merriweather Sans",sans-serif}
  .contacts{position:absolute;left:57px;top:328px;list-style:none}
  .contacts li{display:flex;align-items:center;height:33.5px;font:400 23px/1 "Open Sans",sans-serif;color:var(--text-soft)}
  .contacts svg{width:18px;height:18px;margin:0 22px 0 3px;fill:var(--text-soft)}
  .address{position:absolute;left:57px;top:506px;font:400 23px/33px "Open Sans",sans-serif;color:var(--address)}
  .brand{position:absolute;left:590px;top:436px;display:flex;align-items:center;gap:16px}
  .brand__mark{width:30px;height:30px;background:var(--logo-blue)}
  .brand__name{font:700 62px/1 "Open Sans",sans-serif;color:var(--logo-blue);letter-spacing:1px}
</style>
</head>
<body>
  <section class="card" aria-label="Business card front">
    <svg class="card__band" viewBox="0 0 1040 620" aria-hidden="true">
      <polygon points="0,0 687,0 532,620 0,620" fill="var(--brand-blue)"/>
    </svg>

    <div class="holder">
      <h1 class="holder__name">Dana Merrow Hale</h1>
      <p class="holder__title">Managing Director</p>
    </div>

    <h2 class="company">Vantrell Forge Works, Inc.</h2>

    <ul class="contacts">
      <li><svg viewBox="0 0 20 20"><path d="M2 7c0-3 16-3 16 0v2h-4V7H6v2H2zM5 10h10l2 7H3z"/></svg>214-555-0142 (VFW)</li>
      <li><svg viewBox="0 0 20 20"><path d="M6 1h8a1 1 0 0 1 1 1v16a1 1 0 0 1-1 1H6a1 1 0 0 1-1-1V2a1 1 0 0 1 1-1zm1 2v12h6V3zm3 13a1 1 0 1 0 0 2 1 1 0 0 0 0-2z"/></svg>214-555-0187</li>
      <li><svg viewBox="0 0 20 20"><path d="M5 1h10v5H5zM2 7h16v8h-3v4H5v-4H2zm5 6v4h6v-4z"/></svg>214-555-0193</li>
      <li><svg viewBox="0 0 20 20"><path d="M1 4h18v12H1zm2 2v1l7 5 7-5V6l-7 5z"/></svg>www.vantrellforge.com</li>
      <li><svg viewBox="0 0 20 20"><path d="M10 1a9 9 0 1 0 0 18 9 9 0 0 0 0-18zm0 2c1 1 2 3 2 6H8c0-3 1-5 2-6zM3 9c0-2 2-5 4-5-1 1-1 3-1 5zm11 0c0-2 0-4-1-5 2 0 4 3 4 5zM3 11h3c0 2 0 4 1 5-2 0-4-3-4-5zm5 0h4c0 3-1 5-2 6-1-1-2-3-2-6zm6 0h3c0 2-2 5-4 5 1-1 1-3 1-5z"/></svg>dhale@vantrellforge.com</li>
    </ul>

    <p class="address">418 Kestrel Mill Rd., Brantley,<br>Ohio, US 443170</p>

    <div class="brand">
      <span class="brand__mark" aria-hidden="true"></span>
      <span class="brand__name">Vantrell</span>
    </div>
  </section>
</body>
</html>
```